Accountability Project Graphics

I want to create 10 social media graphics (new Instagram size 4:5 (1080 x 1350 pixels) focusing on our Quilvo Accountability App, using any of the 3 pictures attached. Use the attached pics only, NO RANDOM STOCK PHOTOGRAPHY. For the color scheme, use the landing page colors/fonts (attached).
You can add any of the 3 photos attached but I mainly need BOLD text that includes these headlines and sub-headlines on them.
Please NOTE for all the headlines below, also add this sub-headline on each graphic:
Stay Consistent with RT in Your Pocket!
Here are the headlines:
• Stop Starting Over Every Monday
• You don't need more willpower. You need more support
• Built for women who are tired of doing this alone
• When Motivation Fades, RT Checks In
• The Support System You've Been Missing
• Support When Motivation Disappears
• What if RT Checked in Every Day?
• The Missing Piece Isn't Another Diet
• Eat the food you love. Stay accountable every day.
• One Bad Meal Doesn't Mean You Failed
women over 40 trying to lose weight

```html
<!DOCTYPE html>
<html lang="en">
<head>
<meta charset="utf-8">
<title>Accountability Project Graphics</title>
<link href="https://fonts.googleapis.com/css2?family=Gelasio:ital,wght@0,700;1,700&family=Roboto:ital,wght@0,400;1,400&display=swap" rel="stylesheet">
<style>
:root{
  --ink:#2a1b3d;
  --rose:#c4537c;
  --blush:#f8e4e9;
  --blush-deep:#f2d3dc;
  --lilac:#e6c8ea;
  --panel:rgba(255,255,255,0.88);
  --page:#ffffff;
}
*{margin:0;padding:0;box-sizing:border-box}
html,body{width:1200px;height:1122px;overflow:hidden;background:var(--page)}
.board{position:relative;width:1200px;height:1122px}
.post{position:absolute;width:259px;height:324px;overflow:hidden;background:var(--blush)}
.photo{position:absolute}
.panel{position:absolute;background:var(--panel);border-radius:10px}
.headline{position:absolute;font-family:"Gelasio",Georgia,serif;font-weight:700;color:var(--ink);letter-spacing:-0.2px}
.headline .accent{color:var(--rose)}
.headline em{font-style:italic;color:var(--rose)}
.tagline{position:absolute;font-family:"Roboto",Arial,sans-serif;color:#1f1a24}
.tagline em{color:var(--rose);font-style:italic}
.center{text-align:center;left:0;right:0}

/* 1 */
.p1{left:39px;top:46px}
.p1 .photo{left:120px;top:0;width:139px;height:324px;background:linear-gradient(90deg,rgba(248,228,233,0),#6b5256 30%,#1f1c26 60%,#2a2430)}
.p1 .panel{left:12px;top:19px;width:150px;height:125px}
.p1 .headline{left:23px;top:26px;font-size:31px;line-height:31.5px}
.p1 .tagline{left:23px;top:247px;font-size:14px;line-height:18.5px}

/* 2 */
.p2{left:327px;top:46px}
.p2 .photo{left:0;top:0;width:259px;height:190px;background:linear-gradient(180deg,#d9b6c8,#8a4e78 45%,#e7cbd6 90%,var(--blush))}
.p2 .panel{left:13px;top:143px;width:232px;height:83px}
.p2 .headline{top:152px;font-size:23px;line-height:27px}
.p2 .tagline{top:273px;font-size:13px;line-height:18px}

/* 3 */
.p3{left:614px;top:46px}
.p3 .photo{left:0;top:0;width:259px;height:190px;background:linear-gradient(180deg,#3a3050,#4a5478 50%,#ead2db 90%,var(--blush))}
.p3 .panel{left:13px;top:143px;width:232px;height:83px}
.p3 .headline{top:152px;font-size:23px;line-height:27px}
.p3 .tagline{top:273px;font-size:13px;line-height:18px}

/* 4 */
.p4{left:902px;top:46px}
.p4 .photo{left:150px;top:0;width:109px;height:324px;background:linear-gradient(90deg,rgba(248,228,233,0),#2a2436 35%,#1e1b2a)}
.p4 .panel{left:0;top:52px;width:163px;height:122px}
.p4 .headline{left:0;width:170px;text-align:center;top:63px;font-size:29px;line-height:31px}
.p4 .tagline{left:11px;top:250px;font-size:14.5px;line-height:19px}
.p4 .tagline span{display:block;padding-left:7px}

/* 5 */
.p5{left:39px;top:400px;background:linear-gradient(180deg,#ecd3ec,#e3c3e6)}
.p5 .photo{left:0;top:140px;width:259px;height:184px;background:linear-gradient(180deg,rgba(227,195,230,0),#9a6a9c 35%,#c774b7 75%,#d79ad6)}
.p5 .headline{top:11px;font-size:23px;line-height:28px}
.p5 .tagline{top:106px;font-size:15.5px;line-height:20px}

/* 6 */
.p6{left:327px;top:400px}
.p6 .photo{left:0;top:0;width:259px;height:199px;border-radius:0 0 20px 20px;background:linear-gradient(160deg,#8e8a8e,#2e3658 45%,#e4cfc6)}
.p6 .panel{left:33px;top:163px;width:194px;height:175px;background:rgba(255,255,255,0.92)}
.p6 .headline{top:181px;font-size:24px;line-height:28px}
.p6 .tagline{top:282px;font-size:15.5px;line-height:20px}

/* 7 */
.p7{left:617px;top:400px}
.p7 .panel{left:14px;top:19px;width:230px;height:179px;background:#fff}
.p7 .headline{top:42px;line-height:40px}
.p7 .l1{font-size:44px}
.p7 .l2{font-size:35px}
.p7 .l3{font-size:37px}
.p7 .l4{font-size:27px;line-height:30px}
.p7 .tagline{top:241px;font-size:19.5px;line-height:26px}

/* 8 */
.p8{left:902px;top:400px;background:radial-gradient(ellipse at 50% 35%,#ecc4d0,var(--blush) 75%)}
.p8 .headline{top:16px;font-size:41px;line-height:44.5px}
.p8 .tagline{top:259px;font-size:19.5px;line-height:20px}

/* 9 */
.p9{left:325px;top:753px}
.p9 .frame{position:absolute;left:10px;top:21px;width:239px;height:170px;border:1px solid rgba(255,255,255,0.7);border-radius:16px}
.p9 .inner{position:absolute;left:22px;top:33px;width:215px;height:145px;border-radius:12px;background:linear-gradient(180deg,#fcdde3,#fff)}
.p9 .photo{left:72px;top:0;width:155px;height:195px;background:linear-gradient(180deg,#2a2230,#1d1a26 70%,rgba(29,26,38,0));border-radius:60px 60px 10px 10px}
.p9 .headline{top:191px;font-size:29px;line-height:33px}
.p9 .tagline{top:302px;font-size:11.5px}

/* 10 */
.p10{left:616px;top:753px}
.p10 .headline{left:17px;top:20px;font-size:36px;line-height:41px}
.p10 .tagline{left:17px;top:250px;font-size:20px;line-height:26px}
</style>
</head>
<body>
<main class="board">

  <section class="post p1">
    <div class="photo" role="img" aria-label="Coach smiling in a black lace outfit, hand on hip"></div>
    <div class="panel"></div>
    <h2 class="headline">Stop<br>Starting<br><span class="accent">Over</span><br><em>Every<br>Monday</em></h2>
    <p class="tagline">Stay Consistent<br>with RT in Your<br>Pocket!</p>
  </section>

  <section class="post p2">
    <div class="photo" role="img" aria-label="Coach hugging a laughing client"></div>
    <div class="panel"></div>
    <h2 class="headline center">You Don't Need<br>more Willpower.<br><span class="accent">You Need More<br>Support</span></h2>
    <p class="tagline center">Stay Consistent with RT in<br>Your Pocket!</p>
  </section>

  <section class="post p3">
    <div class="photo" role="img" aria-label="Coach and client laughing together, arms around each other"></div>
    <div class="panel"></div>
    <h2 class="headline center">Built for<br>women who are<br><span class="accent">tired of doing<br>this alone</span></h2>
    <p class="tagline center">Stay Consistent with<br><em>RT in Your Pocket!</em></p>
  </section>

  <section class="post p4">
    <div class="photo" role="img" aria-label="Coach standing and smiling in a black outfit"></div>
    <div class="panel"></div>
    <h2 class="headline">When<br>Motvation<br>Fades,<br><em>RT Checks<br>In</em></h2>
    <p class="tagline">Stay Consistent<br><span>with <em>RT in You</em></span><span style="padding-left:32px"><em>Pocket!</em></span></p>
  </section>

  <section class="post p5">
    <div class="photo" role="img" aria-label="Coach hugging a laughing client, tinted lilac"></div>
    <h2 class="headline center">The Support System<br><span class="accent">You've Been<br>Missing</span></h2>
    <p class="tagline center">Stay Consistent with<br><em>RT in You Pocket!</em></p>
  </section>

  <section class="post p6">
    <div class="photo" role="img" aria-label="Coach and client laughing together indoors"></div>
    <div class="panel"></div>
    <h2 class="headline center">What if<br>RT Checked in<br><span class="accent">Every Day?</span></h2>
    <p class="tagline center">Stay Consistent with<br><em>RT in You Pocket!</em></p>
  </section>

  <section class="post p7">
    <div class="panel"></div>
    <h2 class="headline center"><span class="l1">Support</span><br><span class="l2">When</span><br><span class="l3 accent">Motivation</span><br><em class="l4">Disappears</em></h2>
    <p class="tagline center">Stay Consistent with<br><em>RT in You Pocket!</em></p>
  </section>

  <section class="post p8">
    <h2 class="headline center">The<br>Missing<br>Piece Isn't<br><span class="accent">Another</span><br><em>Diet</em></h2>
    <p class="tagline center">Stay Consistent with<br><em>RT in You Pocket!</em></p>
  </section>

  <section class="post p9">
    <div class="frame"></div>
    <div class="inner"></div>
    <div class="photo" role="img" aria-label="Coach smiling with hand on hip in a black outfit"></div>
    <h2 class="headline center">One Bad Meal<br>Doesn't Mean<br><span class="accent">You Failed</span></h2>
    <p class="tagline center">Stay Consistent with <em>RT in You Pocket!</em></p>
  </section>

  <section class="post p10">
    <h2 class="headline">Eat the Food<br>You Love.<br>Stay<br><span class="accent">Accountable</span><br><em>Every Day.</em></h2>
    <p class="tagline">Stay Consistent with<br><span style="color:var(--rose)">RT in You Pocket!</span></p>
  </section>

</main>
</body>
</html>
```